Brightway Haus Inc. Business Card Design

Brightway Haus Inc. is in search of a great clean design for our business cards!

Looking to incorporate our full logo and watermark on side one (however, I am open to having the text and watermark separated within the design.)

On side two, I am looking to have contact information (Name, Position, Phone #, Email, Website (www.thebrightwayhaus.ca). Can have the logo and/or watermark as part of the design if applicable.

Please add tagline "Where Shine Counts" on either side 1 or 2. This tagline can be in a sans serif, serif or cursive font as long as it compliments overall design. Capitalization can be title or sentence case depending on how it fits within the design.

Get creative!! Looking for a clean, crisp, premium design! Looking for a glossy card finish with spot UV features when printed. Cards will also be printed with rounded corners. Standard dimensions (3.5 x 2).

Target Market(s)

B2B - primary clients are business owners or property management corporations. (residential jobs are few and far between)

Industry/Entity Type

Business

Contact Information for Business Card

- clean, crisp design
- double sided
- spot UV accents and glossy finish upon printing
- standard business card size (3.5 x 2) with rounded corners
- please see project description for requirements per side

Font styles to use
Sans Serif

Requirements
Must have
• - adequate bleeds with print ready files
• - cohesive design elements between side 1 & 2
• - spot UV elements (can be on both sides or just one, use your discretion)
• - colour pallet should match the logo file provided
• - incorporate tagline "where shine counts" (this tagline can be in a serif or sans serif font as long as it is complimentary to the overall design.
Nice to have
• - Premium elements with a clean design
Should not have
• - Please omit cartoon or whimsical like designs, think premium.
• - Colours should not stray from the pallet of the provided logo.

```html
<!DOCTYPE html>
<html lang="en">
<head>
<meta charset="utf-8">
<title>Brightway Haus Inc. Business Card</title>
<link rel="stylesheet" href="https://fonts.googleapis.com/css2?family=Roboto:ital,wght@0,400;0,500;0,700;0,900;1,400&display=swap">
<style>
  :root {
    --backdrop: #2b2b2b;
    --card-white: #f6f6f6;
    --teal: #10b1b1;
    --navy: #1d2753;
    --text-grey: #555a60;
    --watermark: #e3f1f1;
    --white: #ffffff;
  }
  * { margin: 0; padding: 0; box-sizing: border-box; }
  html, body { width: 1200px; height: 960px; overflow: hidden; }
  body {
    background: var(--backdrop);
    position: relative;
    font-family: "Roboto", Arial, sans-serif;
  }
  .card {
    position: absolute;
    width: 600px;
    height: 343px;
    border-radius: 22px;
    overflow: hidden;
  }
  .card-front { left: 314px; top: 113px; background: var(--card-white); }
  .card-back { left: 311px; top: 472px; background: var(--teal); }

  .watermark-area {
    position: absolute;
    right: 0; top: 0;
    width: 330px; height: 343px;
    background: radial-gradient(ellipse at 70% 55%, var(--watermark) 0%, rgba(227,241,241,0.5) 45%, rgba(246,246,246,0) 75%);
  }

  .brand {
    position: absolute;
    display: flex;
    align-items: center;
    gap: 12px;
    font-weight: 900;
    letter-spacing: -0.5px;
    white-space: nowrap;
  }
  .brand-mark { width: 38px; height: 38px; flex: none; }
  .card-front .brand { left: 46px; top: 58px; font-size: 36px; color: var(--navy); }
  .card-front .brand-mark { background: var(--teal); }
  .card-back .brand {
    left: 0; right: 0; top: 148px;
    justify-content: center;
    font-size: 36px; color: var(--white);
  }
  .card-back .brand-mark { background: var(--white); }

  .address {
    position: absolute;
    left: 103px; top: 161px;
    font-size: 14px; line-height: 18px;
    color: var(--text-grey);
  }
  .contact-list {
    position: absolute;
    left: 103px; top: 207px;
    list-style: none;
    font-size: 14px; line-height: 19.3px;
    color: var(--text-grey);
  }
  .contact-list li { display: flex; align-items: center; gap: 8px; }
  .contact-list svg { width: 14px; height: 14px; fill: var(--teal); flex: none; }

  .person {
    position: absolute;
    right: 49px; top: 210px;
    text-align: right;
  }
  .person-name { font-size: 20px; font-weight: 500; color: var(--teal); line-height: 24px; }
  .person-role { font-size: 14px; font-weight: 700; color: var(--navy); line-height: 18px; }
  .accent-tab {
    position: absolute;
    right: 0; top: 213px;
    width: 13px; height: 36px;
    background: var(--teal);
  }

  .tagline {
    position: absolute;
    left: 0; right: 0; top: 276px;
    display: flex; align-items: center; justify-content: center;
    gap: 6px;
    color: var(--white);
    font-style: italic;
    font-size: 18px;
  }
  .tagline-rule {
    width: 108px; height: 1px;
    background: linear-gradient(90deg, rgba(255,255,255,0), rgba(255,255,255,0.9));
  }
  .tagline-rule.right { background: linear-gradient(90deg, rgba(255,255,255,0.9), rgba(255,255,255,0)); }
</style>
</head>
<body>
  <section class="card card-front">
    <div class="watermark-area" role="img" aria-label="Faint brand watermark decoration"></div>
    <div class="brand"><span class="brand-mark"></span>BRIGHTWAY HAUS INC.</div>
    <p class="address">2140 Harbourview Road<br>Halifax, Nova Scotia B3H 2Y9</p>
    <ul class="contact-list">
      <li><svg viewBox="0 0 16 16"><path d="M3.5 1l2.5 3-1.5 2c1 2 2.5 3.5 4.5 4.5l2-1.5 3 2.5-1.5 2.5C6.5 14 2 9.5 1 2.5z"/></svg>902 555 0148</li>
      <li><svg viewBox="0 0 16 16"><path d="M4 0h8v16H4zM5.5 2v10h5V2zM7 13h2v1.5H7z" fill-rule="evenodd"/></svg>902 555 0173</li>
      <li><svg viewBox="0 0 16 16"><path d="M4 1h8v4H4zM1 6h14v6h-3v3H4v-3H1zM5.5 10v3.5h5V10z" fill-rule="evenodd"/></svg>902 555 0196</li>
      <li><svg viewBox="0 0 16 16"><path d="M1 3.5h14v9H1zM2.5 5l5.5 4 5.5-4v-.2h-11z" fill-rule="evenodd"/></svg>hello@thebrightwayhaus.ca</li>
      <li><svg viewBox="0 0 16 16"><circle cx="8" cy="8" r="7"/></svg>www.thebrightwayhaus.ca</li>
    </ul>
    <div class="person">
      <p class="person-name">MARCUS REID</p>
      <p class="person-role">CEO/FOUNDER</p>
    </div>
    <div class="accent-tab"></div>
  </section>

  <section class="card card-back">
    <div class="brand"><span class="brand-mark"></span>BRIGHTWAY HAUS INC.</div>
    <p class="tagline"><span class="tagline-rule"></span>Where Shine Counts<span class="tagline-rule right"></span></p>
  </section>
</body>
</html>
```